Kestrel Facilities Business Card Design

We would now like to design business cards with the new Kestrel Facilities logo

Target Market(s)

Professional

Industry/Entity Type

Professional services

Contact Information for Business Card

Employee name, title, phone number, email address, corporate office address and logo.

Font styles to use
Sans Serif

Colors
0054AA
0677BA
7BADD7
CADEEF
E8F1F8

Requirements
Must have
• My logo
Should not have
• any other pictures or images besides my logo

```html
<!DOCTYPE html>
<html lang="en">
<head>
<meta charset="utf-8">
<title>Kestrel Facilities – Business Card</title>
<link rel="stylesheet" href="https://fonts.googleapis.com/css2?family=Arimo:wght@400&family=Oswald:wght@400;500&display=swap">
<style>
  :root {
    --backdrop: #555555;
    --brand-blue: #0280e8;
    --card-white: #ffffff;
    --ink: #111111;
    --card-shadow: rgba(0, 0, 0, 0.85);
  }
  * { margin: 0; padding: 0; box-sizing: border-box; }
  html, body { width: 1065px; height: 1200px; overflow: hidden; }
  body { background: var(--backdrop); position: relative; font-family: "Arimo", Arial, sans-serif; }

  .card {
    position: absolute;
    width: 582px;
    height: 363px;
    box-shadow: 3px 3px 2px var(--card-shadow);
  }
  .card--front {
    left: 292px; top: 218px;
    background: var(--card-white);
    border-radius: 0 182px 182px 0;
  }
  .card--back {
    left: 263px; top: 623px;
    background: var(--brand-blue);
    border-radius: 182px 0 0 182px;
  }

  .contact { position: absolute; left: 28px; top: 88px; color: var(--ink); }
  .contact__name {
    font-family: "Oswald", "Arial Narrow", sans-serif;
    font-weight: 400; font-size: 27px; line-height: 30px;
    color: var(--brand-blue); letter-spacing: -0.3px;
    transform: scaleX(0.82); transform-origin: left;
  }
  .contact__title { font-size: 17px; line-height: 20px; margin-top: 0; }
  .contact__list { list-style: none; margin-top: 14px; }
  .contact__item { display: flex; align-items: center; font-size: 16.5px; line-height: 21.5px; }
  .contact__icon { width: 15px; height: 15px; margin-right: 6px; fill: var(--brand-blue); }
  .contact__accent { color: var(--brand-blue); }
  .contact__address { font-size: 16.5px; line-height: 21.5px; margin-top: 12px; letter-spacing: 0.2px; }

  .brand {
    position: absolute;
    display: flex; align-items: center; gap: 14px;
    font-family: "Oswald", "Arial Narrow", sans-serif;
    font-weight: 500; text-transform: uppercase; line-height: 0.95;
  }
  .brand__mark { width: 34px; height: 34px; flex: none; }
  .brand__name { font-size: 44px; letter-spacing: 1px; }
  .card--front .brand { left: 285px; top: 105px; color: var(--brand-blue); }
  .card--front .brand__mark { background: var(--brand-blue); }
  .card--back .brand { left: 170px; top: 107px; color: var(--card-white); }
  .card--back .brand__mark { background: var(--card-white); }
</style>
</head>
<body>
  <section class="card card--front" aria-label="Business card front">
    <div class="contact">
      <h1 class="contact__name">DANIEL MERCER</h1>
      <p class="contact__title">Managing Director</p>
      <ul class="contact__list">
        <li class="contact__item">
          <svg class="contact__icon" viewBox="0 0 24 24" aria-hidden="true"><path d="M6.6 10.8a15.1 15.1 0 0 0 6.6 6.6l2.2-2.2a1 1 0 0 1 1-.25 11.4 11.4 0 0 0 3.6.57 1 1 0 0 1 1 1V20a1 1 0 0 1-1 1A17 17 0 0 1 3 4a1 1 0 0 1 1-1h3.5a1 1 0 0 1 1 1c0 1.25.2 2.45.57 3.57a1 1 0 0 1-.25 1z"/></svg>
          044-555 018 274
        </li>
        <li class="contact__item">
          <svg class="contact__icon" viewBox="0 0 24 24" aria-hidden="true"><path d="M2 5h20v14H2z M3 6l9 7 9-7" fill="var(--brand-blue)" stroke="#fff" stroke-width="1.4"/></svg>
          info@kestrelfm.com
        </li>
        <li class="contact__item">
          <svg class="contact__icon" viewBox="0 0 24 24" aria-hidden="true"><circle cx="12" cy="12" r="10" fill="none" stroke="var(--brand-blue)" stroke-width="2"/><path d="M2 12h20M12 2v20M4 7h16M4 17h16" stroke="var(--brand-blue)" stroke-width="1.5" fill="none"/><ellipse cx="12" cy="12" rx="4.5" ry="10" fill="none" stroke="var(--brand-blue)" stroke-width="1.5"/></svg>
          www.<span class="contact__accent">kestrelfacilities</span>.com
        </li>
      </ul>
      <p class="contact__address">421, Address line goes here<br>45452,Country Name</p>
    </div>
    <div class="brand">
      <span class="brand__mark" aria-hidden="true"></span>
      <span class="brand__name">Kestrel<br>Facilities</span>
    </div>
  </section>

  <section class="card card--back" aria-label="Business card back">
    <div class="brand">
      <span class="brand__mark" aria-hidden="true"></span>
      <span class="brand__name">Kestrel<br>Facilities</span>
    </div>
  </section>
</body>
</html>
```